Corvin Ridge Software PowerPoint template

We are a software company selling endpoint visibility, access and security technology to enterprise-level IT departments.
Our technology helps organizations gain comprehensive visibility into and control over devices accessing their corporate network so they can quickly identify and address suspicious activity on the network that could lead to potential threats like data breaches.
This technology can cost organizations upwards of $1M - depending on the size of the organization. Our primary clients are Vestral 2,000 companies.
We want a professional, polished PowerPoint template that we can use for all company presentations. Please include:
Title page
Section page
General info page
Thank you page
Logo options and color specs are attached.
Please include our tagline on at least the title page: Discover the edge. Optimize the whole.
Reason: Seeking more options. Looking for a clean design that uses lots of white space.
Software

```html
<!DOCTYPE html>
<html lang="en">
<head>
<meta charset="UTF-8">
<title>Corvin Ridge Software – Title Slide</title>
<link rel="stylesheet" href="https://fonts.googleapis.com/css2?family=Exo+2:wght@400;500&family=Montserrat:wght@400;600;700&display=swap">
<style>
  :root {
    --brand-red: #9b1c1f;
    --brand-copper: #b4563a;
    --text-grey: #6f7073;
    --rule-grey: #8a8a8a;
    --bg-light: #f1f1f1;
    --bg-white: #ffffff;
    --pattern-tone: #e4e4e4;
  }
  * { margin: 0; padding: 0; box-sizing: border-box; }
  html, body { width: 1200px; height: 849px; overflow: hidden; background: var(--bg-white); }
  .slide {
    position: relative;
    width: 1200px;
    height: 849px;
    overflow: hidden;
    background:
      radial-gradient(circle at 1010px 300px, var(--bg-white) 0, var(--bg-white) 200px, rgba(255,255,255,0) 560px),
      linear-gradient(180deg, #f6f6f6 0%, var(--bg-light) 100%);
    font-family: "Montserrat", Arial, sans-serif;
  }
  .pattern-area {
    position: absolute;
    left: 820px;
    top: 0;
    width: 380px;
    height: 370px;
    background: radial-gradient(ellipse at 70% 35%, var(--pattern-tone) 0%, rgba(228,228,228,0.45) 45%, rgba(255,255,255,0) 75%);
  }
  .tagline {
    position: absolute;
    left: 131px;
    top: 168px;
    font-family: "Exo 2", Arial, sans-serif;
    font-weight: 400;
    font-size: 69px;
    line-height: 72px;
    color: var(--brand-red);
    letter-spacing: 0.5px;
  }
  .presenter {
    position: absolute;
    left: 132px;
    top: 356px;
    font-weight: 600;
    font-size: 22px;
    color: var(--text-grey);
  }
  .date {
    position: absolute;
    left: 132px;
    top: 395px;
    font-weight: 400;
    font-size: 19px;
    color: var(--text-grey);
  }
  .footer-rule {
    position: absolute;
    left: 133px;
    top: 739px;
    width: 549px;
    height: 1px;
    background: var(--rule-grey);
  }
  .website {
    position: absolute;
    left: 133px;
    top: 756px;
    font-weight: 700;
    font-size: 15px;
    color: var(--brand-red);
    letter-spacing: -0.2px;
  }
  .brand-mark {
    position: absolute;
    left: 730px;
    top: 700px;
    width: 56px;
    height: 56px;
    border-radius: 50%;
    background: var(--brand-copper);
    opacity: 0.85;
  }
  .brand-name {
    position: absolute;
    left: 810px;
    top: 696px;
    color: var(--brand-red);
    font-family: "Montserrat", Arial, sans-serif;
    font-weight: 600;
    text-transform: uppercase;
  }
  .brand-name .line-1 { display: block; font-size: 33px; letter-spacing: 3px; line-height: 38px; }
  .brand-name .line-2 { display: block; font-size: 22px; letter-spacing: 15.5px; line-height: 30px; }
</style>
</head>
<body>
  <main class="slide">
    <div class="pattern-area" role="img" aria-label="Decorative pattern of light grey outlined circles"></div>

    <h1 class="tagline">DISCOVER THE EDGE,<br>OPTIMIZE THE WHOLE</h1>
    <p class="presenter">NAME OF THE PRESENTEE</p>
    <p class="date">DATE : MM DD YY</p>

    <div class="footer-rule"></div>
    <p class="website">WWW.CORVINRIDGESOFTWARE.COM</p>

    <div class="brand-mark" aria-hidden="true"></div>
    <p class="brand-name"><span class="line-1">Corvin Ridge</span><span class="line-2">Software</span></p>
  </main>
</body>
</html>
```